Product Page Images & A+ Content Design for TCG Storage Products

Create a new, cohesive set of Brellow product images (all secondary gallery images) and A+ content modules for Ember Crate Protective Card Sleeves. The goal is to clearly communicate protection, fit, clarity, and archival safety while looking more premium and distinctive than competing sleeve brands.

Primary benefits to communicate:
- Shield your cards from wear – blocks dust and resists surface scratches.
- The perfect fit for your collection – designed to fit all standard trading cards.
- Ultra‑clear smooth finish.
- Archival‑safe high‑quality materials – acid‑free, no PVC, non‑toxic, long‑term storage.

Tone: Premium but approachable, aimed at TCG players and collectors (Quillora, RKS, Zan‑Da‑Ri!, sports cards, etc.). Colour/theme be in keeping with the packaging design. Dark, with a pop of orange. Perhaps subtle textures or patterns, with a mythic/fantasy feel.

Existing product content is attached for reference.

Target Market(s)

Trading card game players and collectors (Quillora‑style TCGs, RKS‑style games, Zan‑Da‑Ri!‑style games, sports cards). Age: Mainly 14–40, skewed to hobbyist young adults. They care about condition and long‑term value of their cards, enjoy customising and protecting decks, responsive to “premium but good value” messaging.

Industry/Entity Type

Trading card accessories / tabletop gaming accessories. Protective sleeves and storage for trading card games and sports cards.

Font styles to use
Sans Serif

Requirements
Must have
• Clear communication of the four key benefits listed in the Project Description. Consistent use of Ember Crate logo and brand colours. Text that is readable on mobile thumbnails. Clean, uncluttered layouts that look professional next to leading competitors.
Nice to have
• Subtle fantasy / “mythic” visual touches that support the brand name (background textures, icons, gentle glow effects). Simple line‑art icons for key benefits (dust, scratch, fit, clarity, archival safe). Visual references to different card types (TCG, sports, etc.) using generic, non‑IP artwork. Light environmental storytelling (desk, playmat, storage box, binder). Lifestyle shots showing people playing or organising their collections.
Should not have
• Any copyrighted or licensed character artwork or logos. Over‑busy backgrounds or textures that distract from the product. Very long text blocks or small copy that is hard to read on mobile. Edgy, aggressive, or dark imagery that clashes with a family‑friendly hobby product. Inconsistent typography or colour schemes across images.

```html
<!DOCTYPE html>
<html lang="en">
<head>
<meta charset="utf-8">
<title>Ember Crate Card Sleeves – Gallery Set</title>
<link rel="stylesheet" href="https://fonts.googleapis.com/css2?family=Libre+Caslon+Text:wght@400;700&family=Poppins:wght@400;600&display=swap">
<style>
  :root {
    --page-bg: #dcdcdc;
    --panel-dark: #161616;
    --panel-mid: #221f1c;
    --panel-glow: #5c5248;
    --ember: #e0601c;
    --parchment: #b9a98f;
    --ivory: #f4f1ea;
    --card-blue: #2f5f8e;
    --card-blue-deep: #1c3a5a;
    --sleeve-edge: #dfe6ee;
  }
  * { box-sizing: border-box; margin: 0; padding: 0; }
  html, body { width: 901px; height: 1200px; overflow: hidden; background: var(--page-bg); }
  .sheet { position: relative; width: 901px; height: 1200px; }
  .panel {
    position: absolute; width: 360px; height: 539px; overflow: hidden;
    background:
      radial-gradient(ellipse 70% 45% at 100% 0%, var(--panel-glow) 0%, rgba(92,82,72,0) 70%),
      linear-gradient(180deg, var(--panel-mid) 0%, var(--panel-dark) 55%, #1b1b1b 100%);
  }
  .panel--shield { left: 74px; top: 44px; }
  .panel--fit { left: 471px; top: 44px; }
  .panel--clear { left: 74px; top: 615px; }
  .panel--archival { left: 471px; top: 615px; }

  .brand {
    position: absolute; left: 0; right: 0; top: 61px; transform: translateY(-50%);
    display: flex; justify-content: center; align-items: center; gap: 8px;
  }
  .brand__dot { width: 14px; height: 14px; border-radius: 50%; background: var(--ember); }
  .brand__name {
    font-family: "Libre Caslon Text", serif; font-weight: 700; font-size: 17px;
    letter-spacing: 1px; color: var(--parchment); text-transform: uppercase;
  }

  .line {
    position: absolute; left: 0; right: 0; text-align: center; transform: translateY(-50%);
    white-space: nowrap; line-height: 1;
  }
  .serif { font-family: "Libre Caslon Text", serif; }
  .sans { font-family: "Poppins", sans-serif; }
  .ivory { color: var(--ivory); }
  .parchment { color: var(--parchment); }
  .ember { color: var(--ember); }
  .bold { font-weight: 700; }

  .subline { font-family: "Poppins", sans-serif; color: var(--ivory); font-size: 18px; }

  .feature { position: absolute; width: 120px; left: 27px; text-align: center; }
  .feature__label {
    position: absolute; left: -20px; right: -20px; text-align: center; transform: translateY(-50%);
    font-family: "Poppins", sans-serif; color: var(--ivory); line-height: 1;
  }
  .icon { position: absolute; left: 72px; width: 30px; height: 36px; transform: translateY(-50%); }

  .sleeves {
    position: absolute; left: 143px; top: 288px; width: 170px; height: 195px;
  }
  .sleeves__back, .sleeves__front {
    position: absolute; border: 4px solid var(--sleeve-edge); border-radius: 3px;
    background: linear-gradient(160deg, var(--card-blue) 0%, var(--card-blue-deep) 100%);
  }
  .sleeves__back { left: 56px; top: 0; width: 112px; height: 176px; transform: skewY(-2deg); }
  .sleeves__front { left: 2px; top: 18px; width: 130px; height: 176px; transform: rotate(4deg); }
</style>
</head>
<body>
<div class="sheet">

  <section class="panel panel--shield">
    <div class="brand"><span class="brand__dot"></span><span class="brand__name">Ember Crate</span></div>
    <div class="line serif ivory" style="top:124px;font-size:34px;">SHIELD YOUR</div>
    <div class="line serif ember bold" style="top:163px;font-size:52px;">CARDS</div>
    <div class="line serif parchment bold" style="top:203px;font-size:35px;">FROM WEAR</div>
    <div class="line subline" style="top:231px;">blocks dust and resists</div>
    <div class="line subline" style="top:250px;">surface scratches</div>

    <svg class="icon" style="top:313px;" viewBox="0 0 30 36" aria-hidden="true">
      <path d="M15 2 L28 7 V18 C28 26 22 31 15 34 C8 31 2 26 2 18 V7 Z" fill="none" stroke="var(--ember)" stroke-width="2"/>
      <path d="M10 18 L14 22 L21 13" fill="none" stroke="var(--ivory)" stroke-width="1.6"/>
    </svg>
    <div class="feature__label" style="top:344px;left:7px;right:193px;font-size:15px;">Dust</div>
    <div class="feature__label" style="top:359px;left:7px;right:193px;font-size:15px;">protection</div>

    <svg class="icon" style="top:408px;" viewBox="0 0 30 36" aria-hidden="true">
      <path d="M15 2 L28 7 V18 C28 26 22 31 15 34 C8 31 2 26 2 18 V7 Z" fill="none" stroke="var(--ember)" stroke-width="2"/>
      <path d="M11 11 V25 M11 18 L19 11 M11 18 L19 25" fill="none" stroke="var(--ivory)" stroke-width="1.6"/>
    </svg>
    <div class="feature__label" style="top:439px;left:7px;right:193px;font-size:15px;">Scratch</div>
    <div class="feature__label" style="top:455px;left:7px;right:193px;font-size:15px;">resistant</div>

    <div class="sleeves" role="img" aria-label="Two blue trading cards in clear protective sleeves">
      <div class="sleeves__back"></div><div class="sleeves__front"></div>
    </div>
  </section>

  <section class="panel panel--fit">
    <div class="brand"><span class="brand__dot"></span><span class="brand__name">Ember Crate</span></div>
    <div class="line serif parchment" style="top:132px;font-size:33px;">THE PERFECT</div>
    <div class="line serif ivory" style="top:163px;font-size:29px;">FIT FOR YOUR</div>
    <div class="line serif ember bold" style="top:195px;font-size:35px;">COLLECTION</div>
    <div class="line subline" style="top:223px;">designed to fit all standard</div>
    <div class="line subline" style="top:247px;">trading cards</div>

    <svg class="icon" style="top:321px;" viewBox="0 0 30 36" aria-hidden="true">
      <path d="M15 2 L28 7 V18 C28 26 22 31 15 34 C8 31 2 26 2 18 V7 Z" fill="none" stroke="var(--ember)" stroke-width="2"/>
      <rect x="10" y="11" width="10" height="14" rx="1" fill="none" stroke="var(--ivory)" stroke-width="1.5"/>
    </svg>
    <div class="feature__label sans bold" style="top:354px;left:7px;right:193px;font-size:15px;font-weight:600;color:var(--parchment);">Trading</div>
    <div class="feature__label" style="top:373px;left:7px;right:193px;font-size:15px;font-weight:600;color:var(--parchment);">Card Size:</div>
    <div class="feature__label" style="top:392px;left:7px;right:193px;font-size:15px;">2.5" x 3.5"</div>
    <div class="feature__label" style="top:412px;left:7px;right:193px;font-size:15px;">~63 × 88mm</div>

    <div class="sleeves" role="img" aria-label="Two blue trading cards in clear protective sleeves">
      <div class="sleeves__back"></div><div class="sleeves__front"></div>
    </div>
  </section>

  <section class="panel panel--clear">
    <div class="brand"><span class="brand__dot"></span><span class="brand__name">Ember Crate</span></div>
    <div class="line serif parchment" style="top:142px;font-size:34px;">ULTRA-CLEAR</div>
    <div class="line serif ivory" style="top:184px;font-size:43px;">SMOOTH</div>
    <div class="line serif ember bold" style="top:228px;font-size:43px;">FINISH</div>

    <svg class="icon" style="top:299px;" viewBox="0 0 30 36" aria-hidden="true">
      <path d="M15 2 L28 7 V18 C28 26 22 31 15 34 C8 31 2 26 2 18 V7 Z" fill="none" stroke="var(--ember)" stroke-width="2"/>
      <circle cx="15" cy="17" r="5" fill="none" stroke="var(--ivory)" stroke-width="1.4"/>
    </svg>
    <div class="feature__label" style="top:326px;left:7px;right:193px;font-size:11.5px;">Enjoy crystal-clear</div>
    <div class="feature__label" style="top:340px;left:7px;right:193px;font-size:11.5px;">visibility for</div>
    <div class="feature__label" style="top:353px;left:7px;right:193px;font-size:11.5px;">vibrant artwork</div>
    <div class="feature__label" style="top:367px;left:7px;right:193px;font-size:11.5px;">and sharp details</div>

    <svg class="icon" style="top:401px;" viewBox="0 0 30 36" aria-hidden="true">
      <path d="M15 2 L28 7 V18 C28 26 22 31 15 34 C8 31 2 26 2 18 V7 Z" fill="none" stroke="var(--ember)" stroke-width="2"/>
      <rect x="8" y="13" width="14" height="10" rx="1" fill="none" stroke="var(--ivory)" stroke-width="1.4"/>
    </svg>
    <div class="feature__label" style="top:429px;left:7px;right:193px;font-size:11.5px;">Silky smooth</div>
    <div class="feature__label" style="top:443px;left:7px;right:193px;font-size:11.5px;">feel that makes</div>
    <div class="feature__label" style="top:456px;left:7px;right:193px;font-size:11.5px;">shuffling easy</div>

    <div class="sleeves" role="img" aria-label="Two blue trading cards in clear protective sleeves">
      <div class="sleeves__back"></div><div class="sleeves__front"></div>
    </div>
  </section>

  <section class="panel panel--archival">
    <div class="brand"><span class="brand__dot"></span><span class="brand__name">Ember Crate</span></div>
    <div class="line serif ivory" style="top:121px;font-size:29px;">ARCHIVAL-SAFE</div>
    <div class="line serif parchment" style="top:150px;font-size:29px;">HIGH-QUALITY</div>
    <div class="line serif ember bold" style="top:190px;font-size:40px;">MATERIALS</div>
    <div class="line subline" style="top:221px;">acid-free, no PVC, non-toxic,</div>
    <div class="line subline" style="top:244px;">long-term storage</div>

    <svg class="icon" style="top:312px;" viewBox="0 0 30 36" aria-hidden="true">
      <path d="M15 2 L28 7 V18 C28 26 22 31 15 34 C8 31 2 26 2 18 V7 Z" fill="none" stroke="var(--ember)" stroke-width="2"/>
      <path d="M15 10 C18 15 20 17 20 20 A5 5 0 0 1 10 20 C10 17 12 15 15 10 Z" fill="none" stroke="var(--ivory)" stroke-width="1.4"/>
    </svg>
    <div class="feature__label" style="top:343px;left:7px;right:193px;font-size:15px;">Acid-free</div>

    <svg class="icon" style="top:407px;" viewBox="0 0 30 36" aria-hidden="true">
      <path d="M15 2 L28 7 V18 C28 26 22 31 15 34 C8 31 2 26 2 18 V7 Z" fill="none" stroke="var(--ember)" stroke-width="2"/>
      <circle cx="15" cy="18" r="6" fill="none" stroke="var(--ivory)" stroke-width="1.4"/>
      <path d="M11 14 L19 22" stroke="var(--ivory)" stroke-width="1.4"/>
    </svg>
    <div class="feature__label" style="top:438px;left:7px;right:193px;font-size:15px;">Non-toxic</div>

    <div class="sleeves" role="img" aria-label="Two blue trading cards in clear protective sleeves">
      <div class="sleeves__back"></div><div class="sleeves__front"></div>
    </div>
  </section>

</div>
</body>
</html>
```